Family business needs stationery redesign with new logo

Family owned company, established in 1987 wanting a brand 'refresh'. We are an electrical, refrigeration and construction company based in the Barkly Region Northern Territory, Australia. We have a new logo we would like to use which is uploaded along with our current letterhead and email signature. We are also dropping the word 'contractors' so please do not include this on any designs. Please note also, the 'orange' color used in our logo and designs should be Northern Territory red ochre which is as follows:

RGB (Hex): #C75B12
PantoneĀ® 159 C
CMYK: 1 / 74 / 100 / 7

We are needing our stationery redesigned using our new logo. Please include letterheads, business cards, envelopes, and email signatures.

We currently use our business letterheads for quotations, invoices, letters, HR matters, and internal memos.

We also need a separate simplified letterhead for internal paperwork such as employee leave forms, meeting agendas, and meeting minutes etc.

Reason: Needing more submissions of full package designs. We are wanting all our stationery, including business cards, letterheads, email signatures, envelopes, etc to be cohesive. We also require ALL the information, as supplied on our template letterhead, to be included on the new letterhead designs. including electrical license no.etc Thank you, R&W

Reason: needing more time as work has got in the way of looking over designs. A lot of designs not meeting the brief/criteria.

Industry/Entity Type

Business

Colors
0355a3
f37122

Requirements
Must have
• The 'orange' color used in the designs should be Northern Territory red ochre which is as follows:
• RGB (Hex): #C75B12
• PantoneĀ® 159 C
• CMYK: 1 / 74 / 100 / 7
• ***MUST INCLUDE ALL INFORMATION THAT IS ON OUR CURRENT LETTERHEAD***
Should not have
• Please do not include the word 'contractors'

```html
<!DOCTYPE html>
<html lang="en">
<head>
<meta charset="utf-8">
<title>R&amp;W Stationery</title>
<link href="https://fonts.googleapis.com/css2?family=Source+Sans+3:wght@400;600;700&display=swap" rel="stylesheet">
<style>
:root{
  --navy:#1b2d6b;
  --ochre:#c75b12;
  --paper:#ffffff;
  --card:#f7f7f7;
  --ink:#333333;
  --bg:#dcdcdc;
  --rule:#d0d0d0;
}
*{box-sizing:border-box;margin:0;padding:0}
html,body{width:1200px;height:715px;overflow:hidden}
body{background:var(--bg);font-family:"Source Sans 3",sans-serif;color:var(--ink);position:relative}
a{color:inherit;text-decoration:none}
.piece{position:absolute;box-shadow:0 2px 5px rgba(0,0,0,.25)}
.wordmark{font-weight:700;color:var(--navy);letter-spacing:1px;line-height:1;text-align:center;white-space:nowrap}
.wordmark.light{color:#fff}

/* letterhead */
.letterhead{left:188px;top:68px;width:440px;height:618px;background:var(--paper)}
.letterhead .wordmark{position:absolute;left:0;right:0;top:42px;font-size:40px}
.letterhead .tagline{position:absolute;left:0;right:0;top:97px;text-align:center;font-size:10px;color:var(--navy)}
.letterhead .body{position:absolute;left:32px;width:378px;top:222px;font-size:7.6px;line-height:9.6px;color:var(--ink)}
.letterhead .body p{margin-bottom:9.6px}
.letterhead .signoff{position:absolute;left:32px;top:404px;font-size:7.6px}
.letterhead .footer{position:absolute;left:0;right:0;top:568px;text-align:center;font-size:7.6px;line-height:10.8px;color:var(--ink)}
.footer b{color:var(--ochre);font-weight:600}

/* business cards */
.card{width:240px;height:136px;border-radius:8px}
.card-white{background:var(--card);left:48px;top:160px}
.card-navy{background:var(--navy)}
.card-navy.one{left:48px;top:325px}
.card-navy.two{left:48px;top:482px}
.card-navy .wordmark{position:absolute;left:0;right:0;top:48px;font-size:38px}
.card-navy .est{position:absolute;left:0;right:0;top:110px;text-align:center;font-size:9.5px;letter-spacing:.5px;color:#fff}
.card-navy.two .est{color:var(--ochre)}
.card-logo{position:absolute;font-size:28px}
.divider{position:absolute;width:1px;background:var(--rule)}
.contact{position:absolute;font-size:6.6px;line-height:9px;white-space:nowrap}
.contact .name{font-size:9.5px;font-weight:600;color:var(--navy);line-height:11px}
.contact .role{color:var(--ochre);margin-bottom:4px}
.contact .addr{margin-bottom:4px}
.contact li{list-style:none;display:flex;align-items:center;gap:3px}
.contact svg{width:6px;height:6px;fill:var(--navy)}
.card-white .card-logo{left:18px;top:58px;width:88px}
.card-white .divider{left:119px;top:30px;height:80px}
.card-white .contact{left:135px;top:31px}
.card-wide{background:var(--card);left:748px;top:44px;width:284px;height:138px}
.card-wide .card-logo{left:26px;top:56px;width:100px;font-size:32px}
.card-wide .divider{left:144px;top:18px;height:102px}
.card-wide .contact{left:163px;top:24px;font-size:7.4px;line-height:10.4px}
.card-wide .contact .name{font-size:11px;line-height:12px}
.card-wide svg{width:7px;height:7px}

/* envelopes */
.envelope-back{left:642px;top:210px;width:517px;height:232px;background:var(--paper);overflow:hidden}
.envelope-back svg.folds{position:absolute;inset:0}
.envelope-back .wordmark{position:absolute;left:0;right:0;top:30px;font-size:30px;color:#fff}
.envelope-front{left:642px;top:456px;width:518px;height:232px;background:var(--paper)}
.envelope-front .wordmark{position:absolute;left:24px;top:34px;font-size:34px;text-align:left}
.envelope-front .return{position:absolute;left:25px;top:189px;font-size:8px;line-height:11px;color:var(--ink)}
</style>
</head>
<body>

<section class="piece letterhead">
  <div class="wordmark">R&amp;W</div>
  <div class="tagline">Electrical - Refrigeration - Building Services</div>
  <div class="body">
    <p>Lorem ipsum dolor sit amet, consectetur adipiscing elit. Donec orci purus, luctus vitae dignissim eu, iaculis sed purus. Vivamus faucibus, ipsum nec aliquet viverra, leo mauris condimentum ligula, sit amet sagittis enim ligula quis arcu. Nam egestas tortor id nisi porttitor mattis. In tortor ante, ultricies in suscipit a, tempus non massa. Vivamus et auctor mi.</p>
    <p>Nulla facilisi. Aenean id ligula a. Phasellus nec eros mauris, et scelerisque orci. Donec malesuada orci vitae nulla accumsan scelerisque. Quisque accumsan iaculis magna sit amet fringilla. Maecenas consequat, magna eget tincidunt rutrum, mi rutrum mi, id feugiat ante nisi eu risus. Vestibulum nunc orci, rhoncus a placerat in, ultricies varius eros, vel fringilla nisi suscipit eget.</p>
    <p>Curabitur at sagittis nulla at porttitor. Mauris a justo et tellus interdum tristique. Sed id augue vitae urna aliquet a quam. Pellentesque arcu velit, cursus et malesuada ut, consequat et diam. Nullam ullamcorper vitae, rhoncus et arcu. In ultricies ultricies nulla, ut rutrum nisi iaculis at. Donec ornare faucibus.</p>
    <p>Aliquam rhoncus ultricies. Morbi semper, est id tincidunt gravida, sem arcu adipiscing lacus, ac bibendum erat. Quisque nec diam sed risus consectetur a ccumsan quis quis nibh. Vestibulum id purus lorem.</p>
  </div>
  <div class="signoff">Sam Lee</div>
  <div class="footer">
    42 Banks St, PO Box, Dune Creek NT.&nbsp;0800<br>
    ABN 12 345 678 | Refrigerant Trading Authorisation 102938 | NT Electrical License 40512<br>
    <b>P :</b> 08&nbsp;8000&nbsp;1234 &nbsp;<b>F :</b> 08&nbsp;8000&nbsp;5678 &nbsp;<b>E :</b> info@rwservices.com.au &nbsp;<b>W :</b> rwservices.com.au
  </div>
</section>

<svg width="0" height="0" style="position:absolute">
  <defs>
    <symbol id="i-phone" viewBox="0 0 10 10"><path d="M2 0h2l1 3-1.3 1a6 6 0 0 0 2.3 2.3L7 5l3 1v2c0 1-1 2-2 2A8 8 0 0 1 0 2c0-1 1-2 2-2z"/></symbol>
    <symbol id="i-fax" viewBox="0 0 10 10"><rect x="2" y="0" width="6" height="3"/><rect x="0" y="4" width="10" height="6" rx="1"/></symbol>
    <symbol id="i-mail" viewBox="0 0 10 10"><path d="M0 2h10v6H0z M0 2l5 3.5L10 2"/></symbol>
    <symbol id="i-web" viewBox="0 0 10 10"><circle cx="5" cy="5" r="5"/></symbol>
  </defs>
</svg>

<section class="piece card card-white">
  <div class="wordmark card-logo">R&amp;W</div>
  <div class="divider"></div>
  <div class="contact">
    <div class="name">Alan Reed</div>
    <div class="role">CEO/Founder</div>
    <div class="addr">1420 Cedar Row<br>Fairview, Ohio 44021</div>
    <ul>
      <li><svg><use href="#i-phone"/></svg>555 210 4471</li>
      <li><svg><use href="#i-fax"/></svg>555 210 4472</li>
      <li><svg><use href="#i-mail"/></svg>mail@rwsite.com</li>
      <li><svg><use href="#i-web"/></svg>www.rwsite.com</li>
    </ul>
  </div>
</section>

<section class="piece card card-navy one">
  <div class="wordmark light">R&amp;W</div>
  <div class="est">Est. 1987</div>
</section>

<section class="piece card card-navy two">
  <div class="wordmark light">R&amp;W</div>
  <div class="est">Est. 1987</div>
</section>

<section class="piece card-wide">
  <div class="wordmark card-logo">R&amp;W</div>
  <div class="divider"></div>
  <div class="contact">
    <div class="name">Alan Reed</div>
    <div class="role">CEO/Founder</div>
    <div class="addr">1420 Cedar Row<br>Fairview, Ohio 44021</div>
    <ul>
      <li><svg><use href="#i-phone"/></svg>555 210 4471</li>
      <li><svg><use href="#i-fax"/></svg>555 210 4472</li>
      <li><svg><use href="#i-mail"/></svg>mail@rwsite.com</li>
      <li><svg><use href="#i-web"/></svg>www.rwsite.com</li>
    </ul>
  </div>
</section>

<section class="piece envelope-back">
  <svg class="folds" width="517" height="232" viewBox="0 0 517 232">
    <path d="M0 232 L200 84 M517 232 L317 84" stroke="#e4e4e4" stroke-width="2" fill="none"/>
    <path d="M0 0 H517 L505 62 Q500 84 478 84 H39 Q17 84 12 62 Z" fill="var(--ochre)"/>
  </svg>
  <div class="wordmark">R&amp;W</div>
</section>

<section class="piece envelope-front">
  <div class="wordmark">R&amp;W</div>
  <div class="return">42 Banks St, PO Box<br>Dune Creek NT.&nbsp;0800</div>
</section>

</body>
</html>
```